Coffee and Plastics

I am looking for a completely new site that shows the products we have. Our current site is www.velmorebrothersbeans.com. We are open minded to what designers come up with. Our current site is www.velmorebrothersbeans.com. You can you the information from there to start the site. I need these tabs on the main home page. ( Home, Coffee & Tea, Condiments, and Paper and Plastics, and Contact.) You can take photos and info from my Current site. In products page.
I will be uploading info and photo for paper and plastics.
Look and feel
Each slider illustrates characteristics of the customer's brand and the style your logo design should communicate.

```html
<!DOCTYPE html>
<html lang="en">
<head>
<meta charset="utf-8">
<title>Velmore Brothers Coffee</title>
<link href="https://fonts.googleapis.com/css2?family=Kreon:wght@400;500&family=Open+Sans:ital,wght@0,300;0,400;0,600;1,300;1,400;1,600;1,700&display=swap" rel="stylesheet">
<style>
  :root{
    --maroon-dark:#2a0303;
    --maroon:#420909;
    --orange:#f7860f;
    --orange-light:#fb9a1d;
    --logo-gold:#f6a623;
    --brown-btn:#7b3606;
    --ink:#222;
    --ink-soft:#3a3a3a;
    --white:#fff;
  }
  *{margin:0;padding:0;box-sizing:border-box}
  html,body{width:929px;height:1200px;overflow:hidden}
  body{position:relative;background:var(--white);font-family:"Open Sans",sans-serif;color:var(--ink)}
  .top-band{position:absolute;left:0;top:0;width:929px;height:302px;background:linear-gradient(180deg,var(--maroon) 0%,var(--maroon-dark) 100%)}
  .phone{position:absolute;left:532px;top:16px;display:flex;align-items:center;gap:7px;color:var(--white);font-weight:300;font-size:22px;letter-spacing:.2px}
  .phone-icon{width:20px;height:20px;background:var(--orange);border-radius:3px;display:flex;align-items:center;justify-content:center}
  .social{position:absolute;left:739px;top:22px;display:flex;gap:6px}
  .social span{width:14px;height:14px;background:var(--white);border-radius:2px;opacity:.92}
  .brand{position:absolute;left:99px;top:58px;width:245px;font-family:"Kreon",serif;font-size:22px;color:var(--logo-gold);letter-spacing:0;white-space:nowrap}
  .main-nav{position:absolute;left:350px;top:48px;width:478px;height:52px}
  .main-nav svg{position:absolute;left:0;top:0}
  .main-nav ul{position:absolute;left:0;top:0;width:100%;height:100%;list-style:none}
  .main-nav li{position:absolute;top:17px;transform:translateX(-50%);color:var(--white);font-style:italic;font-weight:600;font-size:14px;white-space:nowrap}
  .hero{position:absolute;left:100px;top:100px;width:728px;height:295px;background:
      radial-gradient(ellipse at 78% 42%,#f1e4cf 0%,#c9a37a 18%,transparent 38%),
      radial-gradient(ellipse at 25% 10%,#7a4420 0%,transparent 40%),
      linear-gradient(135deg,#5b2e14 0%,#8d5a36 35%,#4a2411 70%,#2c1308 100%)}
  .hero-caption{position:absolute;left:15px;top:138px;width:306px;height:157px;background:rgba(20,8,4,.78);padding:20px 10px 0 22px}
  .hero-caption p{color:var(--white);font-style:italic;font-weight:300;font-size:11px;line-height:18.6px;letter-spacing:-.35px}
  .btn-learn{display:inline-block;margin-top:9px;background:var(--orange);color:var(--white);font-style:italic;font-weight:700;font-size:11px;padding:5px 18px 6px 18px}
  .hero-dots{position:absolute;left:641px;top:266px;display:flex;gap:5px}
  .hero-dots span{width:15px;height:15px;border-radius:50%;border:2.5px solid var(--orange)}
  .hero-dots span.active{border-color:var(--white)}
  h2{position:absolute;left:100px;font-style:italic;font-weight:400;font-size:19.5px;letter-spacing:-.5px;color:var(--ink)}
  .welcome-title{top:425px}
  .welcome-photo{position:absolute;left:100px;top:471px;width:363px;height:233px;background:linear-gradient(140deg,#6b3b1c 0%,#3d1d0c 45%,#9a7a55 80%,#c7ad86 100%)}
  .welcome-text{position:absolute;left:470px;top:466px;width:362px;font-size:10px;line-height:18.6px;color:var(--ink-soft);letter-spacing:-.4px}
  .welcome-text p+p{margin-top:18.6px}
  .welcome-text em{font-weight:700;color:var(--ink);margin-left:3px}
  .products-title{top:745px}
  .product{position:absolute;top:786px;width:171px}
  .product-photo{width:171px;height:113px}
  .product h3{margin-top:11px;font-weight:400;font-size:10.6px;color:var(--ink-soft);letter-spacing:-.3px;white-space:nowrap}
  .product .meta{margin-top:3px;font-size:8.8px;color:var(--ink-soft);letter-spacing:-.3px;white-space:nowrap}
  .btn-buy{display:inline-block;margin-top:5px;margin-left:1px;background:var(--brown-btn);color:var(--white);font-size:10.5px;padding:5px 11px 6px;letter-spacing:-.2px}
  .divider{position:absolute;left:100px;top:988px;width:728px;height:12px;background:radial-gradient(ellipse at 50% 0%,rgba(0,0,0,.14) 0%,transparent 70%)}
  .clients-title{position:absolute;left:0;top:1011px;width:929px;text-align:center;font-weight:600;font-size:10.5px;color:var(--ink-soft);letter-spacing:-.2px}
  .clients{position:absolute;left:100px;top:1038px;width:728px;height:52px}
  .footer{position:absolute;left:0;top:1101px;width:929px;height:99px;background:var(--maroon-dark)}
  .footer-nav{position:absolute;left:0;top:28px;width:929px;text-align:center;color:var(--white);font-size:11.3px;letter-spacing:-.2px;word-spacing:1px}
  .footer-nav .sep{margin:0 9px}
  .copyright{position:absolute;left:0;top:53px;width:929px;text-align:center;color:var(--white);font-size:11.3px;letter-spacing:-.3px}
</style>
</head>
<body>
  <div class="top-band"></div>

  <div class="phone">
    <span class="phone-icon">
      <svg width="12" height="14" viewBox="0 0 12 14"><path d="M3 1 L5 4 L4 5.5 Q5 8.5 7.5 10 L9 9 L11.5 11 L10 13 Q4 12.5 1.5 3 Z" fill="#fff"/></svg>
    </span>
    1-800-555-0142
  </div>
  <div class="social" aria-label="Social links"><span></span><span></span><span></span><span></span><span></span></div>

  <div class="brand">Velmore Brothers Coffee</div>

  <nav class="main-nav">
    <svg width="478" height="52" viewBox="0 0 478 52"><path d="M22 0 H478 V52 H0 Z" fill="var(--orange)"/></svg>
    <ul>
      <li style="left:78px">Home</li>
      <li style="left:152px">Coffee &amp; Tea</li>
      <li style="left:242px">Condiments</li>
      <li style="left:314px">Paper</li>
      <li style="left:372px">Plastics</li>
      <li style="left:436px">Contact</li>
    </ul>
  </nav>

  <section class="hero" role="img" aria-label="Coffee beans spilling from a burlap sack beside a steaming cup of coffee">
    <div class="hero-caption">
      <p>Lorem Ipsum is simply dummy text of the printing and typesetting industry. Lorem Ipsum has been the industry's standard dummy text ever since the 1500s, when an unknown printer took a galley of type and scrambled</p>
      <span class="btn-learn">Learn More</span>
    </div>
    <div class="hero-dots"><span class="active"></span><span></span><span></span><span></span></div>
  </section>

  <h2 class="welcome-title">Welcome to Velmore Brothers Coffee</h2>
  <div class="welcome-photo" role="img" aria-label="Roasted coffee beans with a metal scoop in a burlap sack"></div>
  <div class="welcome-text">
    <p>We are a family-owned and operated business based in Marlow Creek Texas. Since the opening of Velmore Brothers Coffee plant in 1995, we have become Texas' premier independently owned coffee packaging company. Our success relies solely on the principle of selling only the freshest, highest-quality in-room coffee available.</p>
    <p>Velmore Brothers packages and supplies in-room coffee, tea products, and condiments. Whether we're supplying a 50-room Hotel or a 500-room grand resort, we have the distribution capacity to fill your rooms with the most aromatic and robust coffees and teas available at competitive prices.</p>
    <p>Velmore Brothers is continuously striving for ways to improve quality and product appearance to meet the highest standards in today's franchises and independent hotels. <em>Read More</em></p>
  </div>

  <h2 class="products-title">Our Products</h2>

  <article class="product" style="left:100px">
    <div class="product-photo" role="img" aria-label="Gold compartment tray" style="background:radial-gradient(ellipse at 50% 50%,#c9a54a 0%,#a88a3c 30%,#c9c3bd 55%,#bdb7b1 100%)"></div>
    <h3>1 Cup Filter Pouch Packets (Regular)</h3>
    <div class="meta">100% Arabica |&nbsp; Medium Roast &nbsp;| 250 Count</div>
    <span class="btn-buy">Buy Now</span>
  </article>
  <article class="product" style="left:288px">
    <div class="product-photo" role="img" aria-label="White round sectioned plastic plate" style="background:radial-gradient(ellipse at 50% 48%,#f2f2f2 0%,#dcdcdc 30%,#1a1a1a 52%,#151515 100%)"></div>
    <h3>1 Cup Filter Pouch Packets (Regular)</h3>
    <div class="meta">100% Arabica |&nbsp; Medium Roast &nbsp;| 250 Count</div>
    <span class="btn-buy">Buy Now</span>
  </article>
  <article class="product" style="left:472px">
    <div class="product-photo" role="img" aria-label="Clear plastic compartment tray" style="background:radial-gradient(ellipse at 50% 50%,#cfd2d4 0%,#9a9ea2 30%,#1b1b1b 55%,#141414 100%)"></div>
    <h3>1 Cup Filter Pouch Packets (Regular)</h3>
    <div class="meta">100% Arabica |&nbsp; Medium Roast &nbsp;| 250 Count</div>
    <span class="btn-buy">Buy Now</span>
  </article>
  <article class="product" style="left:657px">
    <div class="product-photo" role="img" aria-label="Paper coffee cup with white lid" style="background:linear-gradient(90deg,#2a2a2a 0%,#d9d9d9 25%,#e8e8e8 40%,#9c7a56 62%,#b99a74 80%,#2a2a2a 100%)"></div>
    <h3>1 Cup Filter Pouch Packets (Regular)</h3>
    <div class="meta">100% Arabica |&nbsp; Medium Roast &nbsp;| 250 Count</div>
    <span class="btn-buy">Buy Now</span>
  </article>

  <div class="divider"></div>
  <div class="clients-title">Serving Fine Establishments Everywhere!</div>
  <svg class="clients" width="728" height="52" viewBox="0 0 728 52" aria-label="Partner hotel badges">
    <rect x="6" y="2" width="78" height="48" rx="8" fill="#233a8b"/>
    <rect x="100" y="8" width="96" height="36" rx="4" fill="#1c1c1c"/>
    <rect x="209" y="7" width="67" height="38" fill="#2a7a3c"/>
    <rect x="292" y="6" width="55" height="40" rx="4" fill="#1f3f8a"/>
    <rect x="359" y="4" width="73" height="44" rx="6" fill="#b31a3a"/>
    <rect x="442" y="4" width="63" height="44" rx="6" fill="#9b1620"/>
    <rect x="520" y="4" width="64" height="44" rx="6" fill="#2a8a4a"/>
    <rect x="597" y="2" width="77" height="48" rx="8" fill="#1d2f80"/>
    <rect x="683" y="1" width="45" height="50" fill="#1f6b3a"/>
  </svg>

  <footer class="footer">
    <div class="footer-nav">Home<span class="sep">|</span>Coffee &amp; Tea<span class="sep">|</span>Condiments<span class="sep">|</span>Paper<span class="sep">|</span>Plastics<span class="sep">|</span>Contact</div>
    <div class="copyright">© Company Name,All Rights Reserved</div>
  </footer>
</body>
</html>
```